Belmont Ridge Business Card Design Project

We have recently rebranded and would like to design new business cards that incorporate the corporate logo - double sided cards with corporate logo on one side and contact details on the other

Target Market(s)

Sophisticated and high net worth investors and finance industry professionals

Industry/Entity Type

Funds Management

Contact Information for Business Card

The card should prominently feature the company name and logo. Other details will be standard contact details for each staff member - name, address, phone, email, website

Colors
0054AA
0677BA
7BADD7
CADEEF
E8F1F8

Requirements
Must have
• Double-sided design with one side prominently featuring the corporate logo and the other side with all standard contact details

```html
<!DOCTYPE html>
<html lang="en">
<head>
<meta charset="utf-8">
<title>Belmont Ridge Business Card</title>
<link href="https://fonts.googleapis.com/css2?family=Jost:wght@400;500&family=Open+Sans:wght@400&display=swap" rel="stylesheet">
<style>
  :root {
    --stage: #ababab;
    --navy: #1f4572;
    --navy-soft: #2b5282;
    --paper: #ffffff;
    --paper-tint: #f2f3f4;
    --ink: #6b6b6b;
    --ink-label: #5f6368;
  }
  html, body {
    margin: 0;
    padding: 0;
    width: 1200px;
    height: 1000px;
    overflow: hidden;
    background: var(--stage);
  }
  .stage {
    position: relative;
    width: 1200px;
    height: 1000px;
  }
  .card {
    position: absolute;
    width: 514px;
    height: 297px;
    box-shadow: 0 18px 40px rgba(0,0,0,0.35);
    overflow: hidden;
  }
  .card--front {
    left: 57px;
    top: 339px;
    background: var(--navy);
  }
  .card--back {
    left: 614px;
    top: 338px;
    background: var(--paper);
  }
  .decor {
    position: absolute;
    right: 0;
    bottom: 0;
  }
  .card--front .decor {
    width: 514px;
    height: 255px;
    background: linear-gradient(160deg, var(--navy) 30%, var(--navy-soft) 100%);
  }
  .card--back .decor {
    width: 370px;
    height: 255px;
    background: linear-gradient(160deg, var(--paper) 30%, var(--paper-tint) 100%);
  }
  .wordmark {
    position: absolute;
    font-family: "Jost", sans-serif;
    font-weight: 500;
    text-transform: uppercase;
    letter-spacing: 0.06em;
    white-space: nowrap;
  }
  .card--front .wordmark {
    right: 49px;
    top: 242px;
    font-size: 16px;
    color: var(--paper);
  }
  .card--back .wordmark {
    left: 45px;
    top: 58px;
    font-size: 15px;
    color: var(--navy);
  }
  .person {
    position: absolute;
    left: 45px;
    top: 104px;
  }
  .person__name {
    margin: 0;
    font-family: "Jost", sans-serif;
    font-weight: 500;
    font-size: 19px;
    letter-spacing: 0.08em;
    color: var(--navy);
    text-transform: uppercase;
    line-height: 1;
  }
  .person__role {
    margin: 5px 0 0;
    font-family: "Jost", sans-serif;
    font-weight: 400;
    font-size: 9.5px;
    letter-spacing: 0.12em;
    color: var(--ink-label);
    text-transform: uppercase;
  }
  .person__rule {
    width: 23px;
    height: 2px;
    margin-top: 7px;
    background: var(--navy);
  }
  .address, .contacts {
    position: absolute;
    left: 44px;
    margin: 0;
    font-family: "Open Sans", sans-serif;
    font-size: 14px;
    color: var(--ink);
    line-height: 17px;
  }
  .address { top: 163px; font-style: normal; }
  .contacts {
    top: 223px;
    list-style: none;
    padding: 0;
  }
  .contacts li {
    display: flex;
    align-items: center;
    gap: 5px;
  }
  .contacts svg {
    width: 11px;
    height: 11px;
    fill: var(--navy);
    flex: none;
    margin-top: 2px;
  }
</style>
</head>
<body>
<main class="stage">
  <section class="card card--front" aria-label="Business card front">
    <div class="decor" role="img" aria-label="Faint large outline of the brand symbol as background decoration"></div>
    <span class="wordmark">Belmont Ridge</span>
  </section>

  <section class="card card--back" aria-label="Business card back">
    <div class="decor" role="img" aria-label="Faint large outline of the brand symbol as background decoration"></div>
    <span class="wordmark">Belmont Ridge</span>
    <div class="person">
      <h1 class="person__name">Daniel Hale</h1>
      <p class="person__role">Portfolio Manager</p>
      <div class="person__rule"></div>
    </div>
    <address class="address">Level 14 Harbour Tower, 52 Kent Street,<br>Sydney NSW 2000</address>
    <ul class="contacts">
      <li>
        <svg viewBox="0 0 12 12" aria-hidden="true"><path d="M2.4 0.6 4.2 2.6 3.3 4a6.5 6.5 0 0 0 4.7 4.7l1.4-0.9 2 1.8-1.2 1.8C5.6 11.6 0.4 6.4 0.6 1.8z"/></svg>
        +02 9450 3176
      </li>
      <li>
        <svg viewBox="0 0 12 12" aria-hidden="true"><path d="M0.5 2.5h11v7h-11z M1 3l5 3.6L11 3" fill="var(--navy)" stroke="#fff" stroke-width="0.9"/></svg>
        invest@belmont-ridge.com
      </li>
      <li>
        <svg viewBox="0 0 12 12" aria-hidden="true"><circle cx="6" cy="6" r="5.4"/><path d="M0.6 6h10.8M6 0.6v10.8M6 0.6c-3 3-3 7.8 0 10.8M6 0.6c3 3 3 7.8 0 10.8M1.6 3.3h8.8M1.6 8.7h8.8" fill="none" stroke="#fff" stroke-width="0.7"/></svg>
        www.belmont-ridge.com
      </li>
    </ul>
  </section>
</main>
</body>
</html>
```